Business Cards for a law firm

Business cards for our law firm. Use our silhoette logo and OAK PARTNERS - check our website (www.oakpartners.example)

Contact Information for Business Card

our silhouette logo, OAK PARTNERS, 800-555-0147, Dorian Pemberton, dorian@oakpartners.example

Requirements
Must have
• our silhouette logo, OAK PARTNERS, 800-555-0147, Dorian Pemberton, dorian@oakpartners.example

```html
<!DOCTYPE html>
<html lang="en">
<head>
<meta charset="utf-8">
<title>Oak Partners – Business Cards</title>
<link href="https://fonts.googleapis.com/css2?family=Cinzel:wght@500;600&family=Arimo:wght@400&display=swap" rel="stylesheet">
<style>
  :root {
    --backdrop: #3b3b3d;
    --navy: #1b2f6e;
    --navy-deep: #14245a;
    --navy-light: #2d4fb0;
    --paper: #ffffff;
    --ghost: #eef0f3;
    --rule: #d4d6da;
    --ink: #4a4a4a;
  }
  * { margin: 0; padding: 0; box-sizing: border-box; }
  html, body { width: 1200px; height: 689px; overflow: hidden; }
  body {
    background: var(--backdrop);
    position: relative;
    font-family: "Arimo", Arial, sans-serif;
  }
  .card {
    position: absolute;
    top: 200px;
    width: 500px;
    height: 290px;
    border-radius: 16px;
    overflow: hidden;
  }
  /* Back of card */
  .card-back { left: 70px; background: var(--navy); }
  .pattern-area {
    position: absolute; inset: 0;
    background: linear-gradient(100deg, var(--navy-deep) 0%, var(--navy) 50%, var(--navy-light) 100%);
  }
  .back-mark {
    position: absolute; right: 30px; top: 40px;
    font-family: "Cinzel", serif; font-weight: 600;
    font-size: 13px; letter-spacing: 2px; color: var(--paper);
  }
  /* Front of card */
  .card-front { left: 630px; background: var(--paper); }
  .figure-area {
    position: absolute; left: 30px; top: 90px; width: 190px; height: 200px;
    background: linear-gradient(180deg, var(--ghost), #f6f7f9);
    border-radius: 60px 60px 0 0;
  }
  .brand {
    position: absolute; right: 40px; top: 50px;
    display: flex; align-items: center; gap: 10px;
  }
  .brand-square { width: 20px; height: 20px; background: var(--navy); }
  .brand-name {
    font-family: "Cinzel", serif; font-weight: 600;
    font-size: 22px; letter-spacing: 2px; color: var(--navy);
  }
  .top-rule {
    position: absolute; left: 40px; right: 30px; top: 110px;
    height: 1px; background: var(--rule);
  }
  .holder-name {
    position: absolute; left: 30px; top: 160px;
    font-family: "Cinzel", serif; font-weight: 600;
    font-size: 22px; letter-spacing: 1.5px; color: var(--navy);
  }
  .contact-rule {
    position: absolute; left: 30px; width: 260px; top: 200px;
    height: 1px; background: var(--rule);
  }
  .contact {
    position: absolute; left: 32px; top: 210px;
    list-style: none; font-size: 13px; color: var(--ink); line-height: 20px;
  }
  .contact li { display: flex; align-items: center; gap: 8px; }
  .contact svg { width: 11px; height: 11px; fill: var(--navy); }
  .web-band {
    position: absolute; right: 0; bottom: 0; width: 220px; height: 34px;
    background: var(--navy);
    clip-path: polygon(12px 0, 100% 0, 100% 100%, 0 100%);
    display: flex; align-items: center; justify-content: flex-end;
    padding-right: 16px;
    color: var(--paper); font-size: 13px;
  }
</style>
</head>
<body>
  <section class="card card-back">
    <div class="pattern-area" role="img" aria-label="Repeating pattern of the firm's silhouette mark in shades of blue"></div>
    <div class="back-mark">OAK PARTNERS</div>
  </section>

  <section class="card card-front">
    <div class="figure-area" role="img" aria-label="Faint large silhouette figures decorating the card"></div>
    <div class="brand">
      <span class="brand-square"></span>
      <span class="brand-name">OAK PARTNERS</span>
    </div>
    <div class="top-rule"></div>
    <h1 class="holder-name">Dorian Pemberton</h1>
    <div class="contact-rule"></div>
    <ul class="contact">
      <li>
        <svg viewBox="0 0 24 24" aria-hidden="true"><path d="M6.6 10.8a15.1 15.1 0 0 0 6.6 6.6l2.2-2.2a1 1 0 0 1 1-.25 11.4 11.4 0 0 0 3.6.57 1 1 0 0 1 1 1V20a1 1 0 0 1-1 1A17 17 0 0 1 3 4a1 1 0 0 1 1-1h3.5a1 1 0 0 1 1 1c0 1.25.2 2.45.57 3.6a1 1 0 0 1-.25 1z"/></svg>
        800-555-0147
      </li>
      <li>
        <svg viewBox="0 0 24 24" aria-hidden="true"><path d="M2 5h20v14H2z M2 5l10 8 10-8" fill="none" stroke="#1b2f6e" stroke-width="2.5"/></svg>
        dorian@oakpartners.example
      </li>
    </ul>
    <div class="web-band">www.oakpartners.example</div>
  </section>
</body>
</html>
```